Business Card Design Project

Looking to update our business cards. We have a logo with our slogan. We are an IT firm so we wouldlike a modern look.

Industry/Entity Type

Business

```html
<!DOCTYPE html>
<html lang="en">
<head>
<meta charset="utf-8">
<title>Lumen Systems Inc – Business Cards</title>
<link href="https://fonts.googleapis.com/css2?family=Josefin+Sans:wght@400;600&family=Open+Sans:wght@400;600;700&display=swap" rel="stylesheet">
<style>
  :root {
    --backdrop: #dcdcdc;
    --card: #fbfbfa;
    --green-dark: #6f8c3c;
    --green: #86a64e;
    --green-light: #b5d15a;
    --ink: #222;
    --ink-soft: #444;
  }
  * { box-sizing: border-box; margin: 0; padding: 0; }
  html, body { width: 1200px; height: 900px; overflow: hidden; }
  body {
    background: var(--backdrop);
    font-family: "Open Sans", Arial, sans-serif;
    position: relative;
  }
  .card {
    position: absolute;
    width: 630px;
    height: 360px;
    background: var(--card);
    box-shadow: 0 10px 28px rgba(0,0,0,.25);
    overflow: hidden;
  }
  .card--front { left: 60px; top: 50px; }
  .card--back { left: 510px; top: 490px; }

  .brand { position: absolute; text-align: center; }
  .brand__name {
    display: flex; align-items: center; justify-content: center; gap: 10px;
    font-family: "Open Sans", Arial, sans-serif;
    font-weight: 600;
    color: var(--green-dark);
    letter-spacing: 3px;
    white-space: nowrap;
  }
  .brand__dot { flex: none; border-radius: 50%; background: var(--green-light); }
  .brand__slogan {
    font-family: "Josefin Sans", Arial, sans-serif;
    font-weight: 600;
    color: #333;
    text-transform: uppercase;
    white-space: nowrap;
  }

  .card--front .brand { left: 0; right: 0; top: 92px; }
  .card--front .brand__name { font-size: 42px; }
  .card--front .brand__dot { width: 22px; height: 22px; }
  .card--front .brand__slogan { font-size: 19px; letter-spacing: 5px; margin-top: 10px; }

  .band {
    position: absolute; left: 0; right: 0; bottom: 0;
    background: linear-gradient(90deg, var(--green-dark), var(--green));
    border-top: 6px solid var(--green-light);
  }
  .card--front .band { height: 86px; display: flex; align-items: center; justify-content: center; }
  .band__web {
    color: #fff; font-size: 19px; letter-spacing: 8px; text-transform: uppercase;
  }

  .card--back .brand { left: 30px; top: 36px; text-align: left; }
  .card--back .brand__name { font-size: 30px; justify-content: flex-start; letter-spacing: 2px; }
  .card--back .brand__dot { width: 16px; height: 16px; }
  .card--back .brand__slogan { font-size: 13px; letter-spacing: 3px; margin-top: 6px; }
  .card--back .band { height: 22px; border-top-width: 4px; }

  .person { position: absolute; right: 36px; top: 130px; text-align: right; }
  .person__name { color: var(--green-dark); font-weight: 700; font-size: 21px; letter-spacing: .5px; text-transform: uppercase; }
  .person__role { color: var(--ink-soft); font-size: 13px; }

  .address { position: absolute; right: 36px; top: 200px; font-size: 13px; color: var(--ink); white-space: nowrap; }
  .company { position: absolute; right: 36px; top: 228px; font-weight: 700; font-size: 17px; color: var(--ink); }

  .contacts { position: absolute; font-size: 13px; line-height: 1.6; color: var(--ink); white-space: nowrap; }
  .contacts--web { left: 36px; top: 232px; }
  .contacts--phone { right: 36px; top: 258px; text-align: right; }
  .contacts dt { display: inline; color: var(--green); }
  .contacts dd { display: inline; }
  .contacts b { font-weight: 700; }
  .contacts .num { color: var(--green); }
</style>
</head>
<body>
  <section class="card card--front">
    <div class="brand">
      <div class="brand__name"><span>LUMEN SYSTEMS INC</span><span class="brand__dot"></span></div>
      <div class="brand__slogan">Smart IT Made Easy</div>
    </div>
    <div class="band"><span class="band__web">www.lumensys.com</span></div>
  </section>

  <section class="card card--back">
    <div class="brand">
      <div class="brand__name"><span>LUMEN SYSTEMS INC</span><span class="brand__dot"></span></div>
      <div class="brand__slogan">Smart IT Made Easy</div>
    </div>

    <div class="person">
      <div class="person__name">Marcus Lee</div>
      <div class="person__role">Service Manager</div>
    </div>

    <div class="address">2240 W. Fulton St Suite 410 Chicago Il. 60612-1101</div>
    <div class="company">LUMEN SYSTEMS INC</div>

    <dl class="contacts contacts--web">
      <div><dt>Email:</dt> <dd><b>info</b>@LumenSys.com</dd></div>
      <div><dt>Web:</dt> <dd>www.<b>LumenSys</b>.com</dd></div>
    </dl>

    <dl class="contacts contacts--phone">
      <div><dt>Phone:</dt> <dd>312 - 740 - <b>LUMN</b> <span class="num">(5866)</span></dd></div>
      <div><dt>Fax:</dt> <dd>312 - 740 - <b>LUMN</b> <span class="num">(5866)</span></dd></div>
    </dl>

    <div class="band"></div>
  </section>
</body>
</html>
```